Gobal construction supply company needs new business card design

I need a business card design for my global supply company using an existing logo. i will be looking to print these on rounded corner cards with the black background version of my logo on the back. on the front white background, my logo again and my simple details.

```html
<!DOCTYPE html>
<html lang="en">
<head>
<meta charset="utf-8">
<title>Northbridge Industrial Supply – Business Card</title>
<link href="https://fonts.googleapis.com/css2?family=Montserrat:wght@700&family=Roboto:wght@400;500&display=swap" rel="stylesheet">
<style>
  :root {
    --bg: #4a4b4e;
    --card-white: #ffffff;
    --ink: #111111;
    --brand-red: #e0141b;
    --text-dark: #1a1a1a;
    --divider: #8a8a8a;
  }
  * { box-sizing: border-box; margin: 0; padding: 0; }
  html, body {
    width: 1200px; height: 1000px; overflow: hidden;
    background: var(--bg);
    font-family: "Roboto", Arial, sans-serif;
  }
  .stage { position: relative; width: 1200px; height: 1000px; }
  .card {
    position: absolute; left: 250px; width: 700px; height: 400px;
    border-radius: 28px; overflow: hidden; background: var(--card-white);
  }
  .card--brand { top: 60px; }
  .card--contact { top: 540px; }

  .mark {
    position: absolute; left: 0; right: 0;
    display: flex; flex-direction: column; align-items: center;
  }
  .mark__row { display: flex; align-items: center; justify-content: center; gap: 12px; }
  .mark__name {
    font-family: "Montserrat", Arial, sans-serif; font-weight: 700;
    font-size: 30px; letter-spacing: 0.3px; text-transform: uppercase; line-height: 1;
    white-space: nowrap; flex: none;
  }
  .mark__dot { width: 22px; height: 22px; border-radius: 50%; background: var(--brand-red); flex: none; }
  .mark__rule { width: 470px; height: 2px; background: var(--brand-red); margin-top: 16px; }

  .card--brand .mark { top: 178px; }
  .card--brand .mark__name { color: var(--ink); }

  .contact__band {
    position: absolute; top: 0; left: 0; right: 0; height: 218px; background: var(--ink);
    border-bottom: 5px solid var(--brand-red);
  }
  .card--contact .mark { top: 98px; }
  .card--contact .mark__name { color: var(--card-white); font-size: 28px; }
  .card--contact .mark__dot { width: 20px; height: 20px; }
  .card--contact .mark__rule { width: 420px; }

  .person { position: absolute; top: 244px; left: 0; right: 0; text-align: center; }
  .person__name {
    font-family: "Montserrat", Arial, sans-serif; font-weight: 700;
    font-size: 24px; color: var(--brand-red); text-transform: uppercase; letter-spacing: 0.5px;
  }
  .person__role { font-size: 12px; font-weight: 500; color: var(--text-dark); text-transform: uppercase; margin-top: 2px; }

  .details {
    position: absolute; top: 308px; left: 0; right: 0;
    display: flex; justify-content: center; gap: 22px;
    font-size: 16px; color: var(--text-dark); line-height: 22px;
  }
  .details__col--left { text-align: right; }
  .details__divider { width: 1px; background: var(--divider); }
  .details__line { display: flex; align-items: center; gap: 8px; white-space: nowrap; }
  .details__col--left .details__line { justify-content: flex-end; }
  .details__line svg { width: 13px; height: 13px; fill: var(--brand-red); flex: none; }
  .details__web strong { color: var(--brand-red); font-weight: 500; }
</style>
</head>
<body>
<main class="stage">

  <section class="card card--brand" aria-label="Card back">
    <div class="mark">
      <div class="mark__row">
        <span class="mark__name">Northbridge Industrial Supply</span>
        <span class="mark__dot"></span>
      </div>
      <div class="mark__rule"></div>
    </div>
  </section>

  <section class="card card--contact" aria-label="Card front">
    <div class="contact__band"></div>
    <div class="mark">
      <div class="mark__row">
        <span class="mark__name">Northbridge Industrial Supply</span>
        <span class="mark__dot"></span>
      </div>
      <div class="mark__rule"></div>
    </div>

    <div class="person">
      <div class="person__name">Marcus Hale</div>
      <div class="person__role">Managing Director</div>
    </div>

    <div class="details">
      <div class="details__col details__col--left">
        <div class="details__line">48 Harbour Road</div>
        <div class="details__line">Westfield, NS 2150</div>
        <div class="details__line">
          <svg viewBox="0 0 24 24" aria-hidden="true"><path d="M6.6 10.8a15.1 15.1 0 0 0 6.6 6.6l2.2-2.2c.3-.3.7-.4 1-.2 1.1.4 2.3.6 3.6.6.6 0 1 .4 1 1V20c0 .6-.4 1-1 1A17 17 0 0 1 3 4c0-.6.4-1 1-1h3.5c.6 0 1 .4 1 1 0 1.3.2 2.5.6 3.6.1.3 0 .7-.2 1z"/></svg>
          +1 (555) 014 2280
        </div>
      </div>
      <div class="details__divider"></div>
      <div class="details__col details__col--right">
        <div class="details__line">
          <svg viewBox="0 0 24 24" aria-hidden="true"><path d="M7 1h10a2 2 0 0 1 2 2v18a2 2 0 0 1-2 2H7a2 2 0 0 1-2-2V3a2 2 0 0 1 2-2zm0 3v14h10V4z"/></svg>
          +1 (555) 014 2280
        </div>
        <div class="details__line">
          <svg viewBox="0 0 24 24" aria-hidden="true"><path d="M2 5h20v14H2zm2 2v.5l8 5 8-5V7l-8 5z"/></svg>
          marcus@northbridgeis.com
        </div>
        <div class="details__line details__web">
          <svg viewBox="0 0 24 24" aria-hidden="true"><path d="M12 2a10 10 0 1 0 0 20 10 10 0 0 0 0-20zm6.9 9h-3a15 15 0 0 0-1.3-6A8 8 0 0 1 18.9 11zM12 4c.9 1.2 1.7 3.8 1.9 7h-3.8C10.3 7.8 11.1 5.2 12 4zM9.4 5A15 15 0 0 0 8.1 11h-3A8 8 0 0 1 9.4 5zM5.1 13h3a15 15 0 0 0 1.3 6A8 8 0 0 1 5.1 13zM12 20c-.9-1.2-1.7-3.8-1.9-7h3.8c-.2 3.2-1 5.8-1.9 7zm2.6-1a15 15 0 0 0 1.3-6h3a8 8 0 0 1-4.3 6z"/></svg>
          <span>www.<strong>northbridgeis</strong>.com</span>
        </div>
      </div>
    </div>
  </section>

</main>
</body>
</html>
```